Gobal construction supply company needs new business card design

I need a business card design for my global supply company using an existing logo. i will be looking to print these on rounded corner cards with the black background version of my logo on the back. on the front white background, my logo again and my simple details.

```html
<!DOCTYPE html>
<html lang="en">
<head>
<meta charset="utf-8">
<title>Meridian Supply Works – Business Cards</title>
<link rel="stylesheet" href="https://fonts.googleapis.com/css2?family=Work+Sans:wght@400;700&family=Arimo:wght@400&display=swap">
<style>
  :root {
    --stage: #1b1b1b;
    --card-dark: #232323;
    --card-dark-glow: #2f2f2f;
    --card-white: #ffffff;
    --accent: #e3141c;
    --ink-light: #ffffff;
    --ink-dark: #222222;
    --ink-muted: #444444;
    --rule: #9a9a9a;
  }
  * { margin: 0; padding: 0; box-sizing: border-box; }
  html, body { width: 1200px; height: 900px; overflow: hidden; background: var(--stage); }
  .stage {
    width: 1200px; height: 900px;
    display: flex; flex-direction: column; align-items: center; justify-content: center;
    gap: 36px;
  }
  .card {
    position: relative;
    width: 700px; height: 400px;
    border-bottom: 6px solid var(--accent);
    border-radius: 12px 12px 0 0;
    box-shadow: 0 10px 24px rgba(0,0,0,.45);
  }
  .card-back {
    background: radial-gradient(ellipse at 75% 40%, var(--card-dark-glow), var(--card-dark) 70%);
  }
  .card-front { background: var(--card-white); }
  .brand {
    position: absolute;
    font-family: "Work Sans", sans-serif; font-weight: 700;
    text-transform: uppercase; letter-spacing: 1px;
    white-space: nowrap; line-height: 1;
  }
  .card-back .brand {
    left: 50%; top: 50%;
    transform: translate(-50%, -50%);
    font-size: 36px; color: var(--ink-light);
  }
  .card-front .brand {
    left: 36px; top: 50%;
    transform: translateY(-50%);
    font-size: 22px; color: var(--ink-dark);
  }
  .divider {
    position: absolute; left: 375px; top: 100px;
    width: 2px; height: 190px; background: var(--rule);
  }
  .details {
    position: absolute; left: 405px; top: 96px;
    font-family: "Work Sans", sans-serif; color: var(--ink-muted);
  }
  .person-name {
    font-family: "Arimo", sans-serif; font-weight: 400;
    font-size: 28px; color: var(--accent); text-transform: uppercase; line-height: 1;
  }
  .person-role { font-size: 17px; margin-top: 4px; letter-spacing: .5px; color: var(--ink-dark); }
  .address { font-size: 17px; line-height: 1.45; margin-top: 18px; letter-spacing: .5px; }
  .contact-list { list-style: none; margin-top: 10px; font-size: 17px; letter-spacing: .5px; }
  .contact-list li { display: flex; align-items: center; gap: 10px; line-height: 1.5; }
  .contact-icon { width: 12px; height: 12px; flex: none; }
</style>
</head>
<body>
<main class="stage">
  <section class="card card-back" aria-label="Card back">
    <p class="brand">Meridian Supply Works</p>
  </section>

  <section class="card card-front" aria-label="Card front">
    <p class="brand">Meridian Supply Works</p>
    <div class="divider"></div>
    <div class="details">
      <p class="person-name">Daniel Carter</p>
      <p class="person-role">Director</p>
      <p class="address">48 Harbour Road Box<br>2710, Lakeview, ON</p>
      <ul class="contact-list">
        <li>
          <svg class="contact-icon" viewBox="0 0 12 12"><path d="M2.5 1 L4.5 1 L5.2 3.5 L4 4.5 Q5 7 7.5 8 L8.5 6.8 L11 7.5 L11 9.5 Q10.5 11 9 11 Q1 10 1 2.5 Q1 1 2.5 1 Z" fill="var(--accent)"/></svg>
          <span>555-210-3846</span>
        </li>
        <li>
          <svg class="contact-icon" viewBox="0 0 12 12"><rect x="1" y="2.5" width="10" height="7" fill="none" stroke="var(--accent)" stroke-width="1.2"/><path d="M1 2.5 L6 6.5 L11 2.5" fill="none" stroke="var(--accent)" stroke-width="1.2"/></svg>
          <span>info@meridiansupply.com</span>
        </li>
        <li>
          <svg class="contact-icon" viewBox="0 0 12 12"><circle cx="6" cy="6" r="5" fill="none" stroke="var(--accent)" stroke-width="1.1"/><ellipse cx="6" cy="6" rx="2.2" ry="5" fill="none" stroke="var(--accent)" stroke-width="1"/><path d="M1 6 H11" stroke="var(--accent)" stroke-width="1"/></svg>
          <span>www.meridiansupply.com</span>
        </li>
      </ul>
    </div>
  </section>
</main>
</body>
</html>
```